Design for Card Attached to Clothes

We sell rhythmic gymnastics apparel and are looking for someone create a card that will be attached to the products. You can see an example of the exact type of apparel in the files, as well as the current card that is attached to it. The design should have space on the top back for the sticker that has UPC and SKU information, as shown in the image attached.
- We would like the front to have our logo
- We would like the image of the girls added on the back
- Would be cool to see the gradient change to the white space on the back where the sticker will go but not required.
-The final card size is 10cm by 6cm, Their should be 2mm loss accounted for cutting the cards within the design. (meaning the design needs to be bigger than 10cm by 6cm to account for printing and cut)
- And the hole size that is at the top center is 3mm in diameter
- Name should be under logo
Access all logo files here https://files.varnolo.net/share/folders/7Kq2mzPtwR4xLbN9cVdHj3sYe81AfoGu?access=open
- Front will have logo
- Back will have image of girls and some creative design that you will create.
Target Market(s)
Females
Industry/Entity Type
Rhythmic Gymnastics

```html
<!DOCTYPE html>
<html lang="en">
<head>
<meta charset="utf-8">
<title>Solvane hang tag – front and back</title>
<link rel="stylesheet" href="https://fonts.googleapis.com/css2?family=Montserrat:wght@500&family=Playfair+Display:ital,wght@1,900&display=swap">
<style>
  :root {
    --backdrop: #3a3a3a;
    --paper: #ffffff;
    --magenta: #ec0c78;
    --violet: #b02f9a;
    --ink: #1a1a1a;
  }
  * { margin: 0; padding: 0; box-sizing: border-box; }
  html, body { width: 1200px; height: 1200px; overflow: hidden; }
  body { background: var(--backdrop); position: relative; }

  .tag {
    position: absolute;
    top: 250px;
    width: 420px;
    height: 700px;
    background: var(--paper);
    box-shadow: 0 18px 40px rgba(0,0,0,0.45);
    overflow: hidden;
  }
  .tag--front { left: 150px; }
  .tag--back { left: 630px; }

  .hang-hole {
    position: absolute;
    left: 50%;
    width: 20px;
    height: 20px;
    margin-left: -10px;
    border-radius: 50%;
  }

  /* front */
  .front-panel {
    position: absolute;
    inset: 24px;
    border-radius: 12px;
    background: linear-gradient(30deg, var(--violet) 0%, #d51d85 35%, var(--magenta) 65%);
  }
  .front-panel .hang-hole { top: 18px; background: var(--paper); }
  .brand-mark {
    position: absolute;
    left: 50%;
    top: 170px;
    width: 180px;
    height: 180px;
    margin-left: -90px;
    border-radius: 50%;
    background: var(--paper);
  }
  .brand-name {
    position: absolute;
    left: 0; right: 0;
    top: 380px;
    text-align: center;
    font-family: "Montserrat", sans-serif;
    font-weight: 500;
    font-size: 54px;
    color: var(--paper);
    letter-spacing: 0.5px;
  }

  /* back */
  .tag--back .hang-hole {
    top: 60px;
    border: 2px solid var(--magenta);
  }
  .accent-band {
    position: absolute;
    left: 270px;
    top: 290px;
    width: 110px;
    height: 370px;
    border-radius: 0 0 55px 55px;
    background: linear-gradient(180deg, rgba(236,12,120,0) 0%, var(--magenta) 30%, #d51d85 100%);
  }
  .athletes-photo {
    position: absolute;
    left: 12px;
    top: 520px;
    width: 396px;
    height: 160px;
  }
  .tagline {
    position: absolute;
    left: 160px;
    top: 500px;
    transform: rotate(-90deg);
    transform-origin: left top;
    white-space: nowrap;
  }
  .tagline-title {
    display: block;
    font-family: "Playfair Display", serif;
    font-style: italic;
    font-weight: 900;
    font-size: 64px;
    line-height: 1.05;
    background: linear-gradient(90deg, var(--violet), var(--magenta));
    -webkit-background-clip: text;
    background-clip: text;
    color: transparent;
  }
  .tagline-sub {
    display: block;
    margin-left: 70px;
    font-family: "Montserrat", sans-serif;
    font-weight: 500;
    font-size: 16px;
    line-height: 1.2;
    color: var(--ink);
    letter-spacing: 0.3px;
  }
</style>
</head>
<body>
  <section class="tag tag--front" aria-label="Tag front">
    <div class="front-panel">
      <span class="hang-hole"></span>
      <span class="brand-mark"></span>
      <p class="brand-name">Solvane</p>
    </div>
  </section>

  <section class="tag tag--back" aria-label="Tag back">
    <span class="hang-hole"></span>
    <span class="accent-band"></span>
    <p class="tagline">
      <span class="tagline-title">Rhythmic</span>
      <span class="tagline-sub">gymnastics apparel</span>
    </p>
    <svg class="athletes-photo" role="img" aria-label="Photo of two rhythmic gymnasts in black leotards stretching with arms raised" viewBox="0 0 396 160">
      <defs>
        <linearGradient id="photoTone" x1="0" y1="0" x2="1" y2="1">
          <stop offset="0" stop-color="#d9c2b4"/>
          <stop offset="0.5" stop-color="#6a5550"/>
          <stop offset="1" stop-color="#1c1c1c"/>
        </linearGradient>
      </defs>
      <rect width="396" height="160" rx="6" fill="url(#photoTone)" opacity="0.85"/>
    </svg>
  </section>
</body>
</html>
```